Professional Services - letterhead / business cards

The company (velmora partners) will provide services to Investment Funds and large investors in Spain. I have recently chosen a logo that I am attaching.

I would like a simple stationary design that i could use as letter head, business cards and "with compliments" cards.

I am not quite sure which color I will mostly use for the logo, in the email signature I will probably lean towards the white background and grey letters. I am attaching my favourite options.

Target Market(s)

Large Multinationals, Investment funds and Law firms

Industry/Entity Type

Business

Requirements
Must have
• my details are:
Luis R. Abadal
Velmora Partners S.L.
Casa de Torrelumbre
Calle de Vientoalto 27
28014 Madrid
T: +34 (91) 387-2265
M: +34 (646) 819-054
e-mail: labadal@velmorapartners.com

```html
<!DOCTYPE html>
<html lang="es">
<head>
<meta charset="utf-8">
<title>Velmora Partners – Business Card</title>
<link rel="stylesheet" href="https://fonts.googleapis.com/css2?family=Questrial&family=Source+Sans+3:wght@400;600&display=swap">
<style>
  :root {
    --navy: #0d1670;
    --ink: #4a4a52;
    --rule: #b9b9bf;
    --paper: #ffffff;
    --backdrop: #e9e8e5;
  }
  * { box-sizing: border-box; margin: 0; padding: 0; }
  html, body {
    width: 1200px;
    height: 588px;
    overflow: hidden;
    background: var(--backdrop);
  }
  .stage {
    position: relative;
    width: 1200px;
    height: 588px;
  }
  .card {
    position: absolute;
    top: 144px;
    width: 520px;
    height: 300px;
    background: var(--paper);
    box-shadow: 0 2px 10px rgba(0,0,0,0.12);
    overflow: hidden;
  }
  .card--front { left: 40px; }
  .card--back { left: 640px; }

  .wordmark {
    font-family: "Questrial", sans-serif;
    font-weight: 400;
    color: var(--navy);
    white-space: nowrap;
    letter-spacing: 0.5px;
  }
  .card--front .wordmark {
    position: absolute;
    left: 0; right: 0;
    top: 112px;
    text-align: center;
    font-size: 40px;
  }
  .website {
    position: absolute;
    left: 0; right: 0;
    top: 170px;
    text-align: center;
    font-family: "Questrial", sans-serif;
    font-size: 12px;
    letter-spacing: 3px;
    color: var(--ink);
  }

  .card--back .wordmark {
    position: absolute;
    left: 40px;
    top: 34px;
    font-size: 38px;
  }
  .contacts {
    position: absolute;
    left: 40px;
    top: 128px;
    list-style: none;
    font-family: "Source Sans 3", sans-serif;
    font-size: 12.5px;
    color: var(--ink);
  }
  .contacts li {
    display: flex;
    align-items: center;
    gap: 8px;
    height: 18px;
  }
  .contacts svg {
    width: 11px;
    height: 11px;
    fill: var(--ink);
    flex: none;
  }
  .holder {
    position: absolute;
    right: 36px;
    top: 186px;
    padding-left: 12px;
    border-left: 1px solid var(--rule);
    font-family: "Source Sans 3", sans-serif;
    color: var(--ink);
    text-align: left;
  }
  .holder__name {
    font-size: 17px;
    font-weight: 600;
    letter-spacing: 0.6px;
    color: var(--navy);
    line-height: 1.1;
  }
  .holder__company {
    font-size: 11px;
    line-height: 1.3;
  }
  .address-band {
    position: absolute;
    left: 0; right: 0;
    top: 226px;
    height: 28px;
    background: var(--navy);
    color: #fff;
    font-family: "Source Sans 3", sans-serif;
    font-size: 12.5px;
    line-height: 28px;
    padding-left: 40px;
    letter-spacing: 0.2px;
  }
</style>
</head>
<body>
<main class="stage">

  <section class="card card--front" aria-label="Business card front">
    <div class="wordmark">velmora partners</div>
    <div class="website">www.velmorapartners.com</div>
  </section>

  <section class="card card--back" aria-label="Business card back">
    <div class="wordmark">velmora partners</div>

    <ul class="contacts">
      <li>
        <svg viewBox="0 0 24 24" aria-hidden="true"><path d="M6.6 10.8a15.1 15.1 0 0 0 6.6 6.6l2.2-2.2a1 1 0 0 1 1-.25 11.4 11.4 0 0 0 3.6.57 1 1 0 0 1 1 1V20a1 1 0 0 1-1 1A17 17 0 0 1 3 4a1 1 0 0 1 1-1h3.5a1 1 0 0 1 1 1c0 1.25.2 2.45.57 3.57a1 1 0 0 1-.25 1z"/></svg>
        <span>+34 (91) 387-2265</span>
      </li>
      <li>
        <svg viewBox="0 0 24 24" aria-hidden="true"><path d="M7 1h10a2 2 0 0 1 2 2v18a2 2 0 0 1-2 2H7a2 2 0 0 1-2-2V3a2 2 0 0 1 2-2zm0 3v14h10V4zm5 15.5a1.2 1.2 0 1 0 0 2.4 1.2 1.2 0 0 0 0-2.4z"/></svg>
        <span>+34 (646) 819-054</span>
      </li>
      <li>
        <svg viewBox="0 0 24 24" aria-hidden="true"><path d="M2 5h20v14H2zm2 2v.5l8 5 8-5V7zm0 2.8V17h16V9.8l-8 5z"/></svg>
        <span>labadal@velmorapartners.com</span>
      </li>
    </ul>

    <div class="holder">
      <div class="holder__name">LUIS R. ABADAL</div>
      <div class="holder__company">Velmora Partners S.L.</div>
    </div>

    <div class="address-band">Casa de Torrelumbre, Calle de Vientoalto 27, 28014 Madrid</div>
  </section>

</main>
</body>
</html>
```